Package of web graphics needed

Utilizing a recently selected logo from a Pixel Harbor contest, we need to have some ads, fb cover, home page slide image created for our new 844-Toll-Free Number Product. Please feel free to check our site at www.vantaquickline.com

You'll find attached the 844 toll free logo in 2 layouts.

Here are the ads and dimensions of each that are needed:
1.)Banners/ads - 468x60
468×60 px
125×125 px
120×600 px
120x90 px
88×31 px button
5.)FB Cover - 851 x 315
6.)Home page slider image - 944 x 328

Here is the text & some ideas to use for these. Feel free to use different versions depending on which ad they work better on:
-

Market Your Business in a Memorable Way – Pre-Order Yours Today, Deadline: Dec. 7th
[include logo]
-
[844 logo] Don't Miss out on your chance to finally get a great vanity!

Order Yours Today
-

Don't Miss out on your chance to finally get a great vanity!
Dec. 7th Deadline to pre-order

Don't Ignore 844!– The newest toll free prefix – Coming Dec. 7th – Get Yours Today

FB COVER guidelines -
Requirements:
Include the logo
Limited Time Left – Get your Reservation in by December 7th

HOME PAGE Image Slide:
Use the logo,

Couple of Ideas we're interested in seeing:

[Billboard sign stock image … with the number 877-Ring-YES on the billboard]
[844 logo and caricature] [1 caricature looking surprised]

Reason: Need more designs to review !

```html
<!DOCTYPE html>
<html lang="en">
<head>
<meta charset="utf-8">
<title>Vanta Quickline – Cover Banner</title>
<link href="https://fonts.googleapis.com/css2?family=Montserrat:wght@400;500;700&display=swap" rel="stylesheet">
<style>
  :root {
    --stage: #22231f;
    --paper: #ffffff;
    --navy: #1b3866;
    --grey-text: #666a6c;
    --green: #5aae2d;
    --green-dark: #3e8f1f;
    --blue: #1f8fd6;
    --teal: #3fc0c9;
    --deep-blue: #1740b8;
  }
  * { margin: 0; padding: 0; box-sizing: border-box; }
  html, body { width: 1200px; height: 750px; overflow: hidden; background: var(--stage); }
  .cover {
    position: absolute; left: 175px; top: 217px;
    width: 851px; height: 315px;
    background: var(--paper); overflow: hidden;
    font-family: "Montserrat", Arial, sans-serif;
  }
  .cover__swoosh { position: absolute; inset: 0; width: 851px; height: 315px; }
  .brand {
    position: absolute; left: 26px; top: 34px;
    display: flex; align-items: center; gap: 12px;
  }
  .brand__mark { width: 26px; height: 26px; background: var(--navy); }
  .brand__name { font-size: 30px; font-weight: 700; color: var(--navy); letter-spacing: -0.5px; }
  .tagline {
    position: absolute; left: 378px; top: 36px;
    font-size: 21px; line-height: 27px; font-weight: 400; color: var(--grey-text);
  }
  .urgency {
    position: absolute; left: 58px; top: 156px;
    font-size: 22px; font-weight: 400; letter-spacing: 2.5px; color: var(--navy);
  }
  .deadline {
    position: absolute; left: 379px; top: 128px;
    padding: 7px 0 0 0; border-left: 2px solid var(--green);
    height: 82px;
  }
  .deadline__box {
    background: var(--green); color: var(--paper);
    width: 273px; height: 67px; padding: 7px 0 0 19px;
    font-size: 19px; line-height: 26px; font-weight: 400;
    box-shadow: 2px 2px 0 rgba(255,255,255,0.8);
  }
  .deadline__box sup { font-size: 11px; }
</style>
</head>
<body>
  <section class="cover">
    <svg class="cover__swoosh" viewBox="0 0 851 315" role="img" aria-label="Abstract flowing blue and green wave backdrop">
      <defs>
        <linearGradient id="waveMain" x1="0" y1="0" x2="1" y2="0">
          <stop offset="0" stop-color="#b9d8ee"/>
          <stop offset="0.3" stop-color="var(--blue)"/>
          <stop offset="0.6" stop-color="var(--teal)"/>
          <stop offset="0.85" stop-color="#2aa58a"/>
          <stop offset="1" stop-color="#9fd23c"/>
        </linearGradient>
        <linearGradient id="waveLow" x1="0" y1="0" x2="1" y2="0">
          <stop offset="0" stop-color="#d9e8f2"/>
          <stop offset="0.5" stop-color="var(--deep-blue)"/>
          <stop offset="1" stop-color="#6cc0e6"/>
        </linearGradient>
      </defs>
      <path d="M0,150 C180,250 420,290 560,250 C680,215 780,130 851,60 L851,315 L0,315 Z" fill="url(#waveMain)" opacity="0.85"/>
      <path d="M700,0 C760,40 820,90 851,110 L851,0 Z" fill="#3a9a2a" opacity="0.8"/>
      <path d="M0,230 C200,300 480,300 620,270 C720,250 800,250 851,260 L851,315 L0,315 Z" fill="url(#waveLow)" opacity="0.75"/>
      <path d="M0,175 C200,260 430,285 560,258 C690,230 790,150 851,95" fill="none" stroke="#ffffff" stroke-width="3" opacity="0.7"/>
    </svg>

    <div class="brand">
      <span class="brand__mark"></span>
      <span class="brand__name">Vanta Quickline</span>
    </div>

    <p class="tagline">Don't Miss out on your chance<br>to finally get a great vanity!</p>

    <p class="urgency">LIMITED TIME LEFT</p>

    <div class="deadline">
      <div class="deadline__box">Get your Reservation<br>in by DECEMBER 7<sup>th</sup></div>
    </div>
  </section>
</body>
</html>
```